Flyer-Design für Kindertagesstätte
Felmriks Spielhafen suchte ein neues Design in der Kategorie Flyer und hat ein Projekt auf grafikwunsch.de gestartet.
Zielgruppe
Wir sind eine Kindertagesstätte und wollen eine Baby-Kind-Spielgruppe jeden Mittwoch in unserer Kita von 09.00 Uhr bis 11.00 Uhr anbieten.
Aufgabenstellung
Unser LOGO muss im Flyer enthalten sein, auf jeden Fall ein Bild wenn möglich mit mehreren Babys/Kleinkindern bis 1,5 Jahre. Wir benötigen den Flyer in DIN lang - bunt - 1 seitig.
Folgender Text sollte enthalten: Baby-Kind-Spielgruppe, jeden mittwoch in unserer Kita 'Felmriks Spielhafen' von 09.00 Uhr bis 11.00 Uhr. Die Spielgruppe wird durch unser ausgebildetes Fachpersonal begleitet.

```html
<!DOCTYPE html>
<html lang="de">
<head>
<meta charset="utf-8">
<title>Felmriks Spielhafen – Baby-Kind-Spielgruppe</title>
<link href="https://fonts.googleapis.com/css2?family=Source+Sans+3:wght@400;600;700;800&display=swap" rel="stylesheet">
<style>
  :root {
    --bg: #e9e9e9;
    --paper: #ffffff;
    --maroon: #5b1a14;
    --teal: #1b9890;
    --magenta: #b0237e;
    --orange: #e0812a;
    --blue: #1b95d4;
    --ink: #1b1b1b;
    --white: #ffffff;
  }
  * { box-sizing: border-box; margin: 0; padding: 0; }
  html, body {
    width: 1200px; height: 800px; overflow: hidden;
    background: var(--bg);
    font-family: "Source Sans 3", "Source Sans Pro", sans-serif;
  }
  .flyer {
    position: absolute; left: 420px; top: 20px;
    width: 360px; height: 760px;
    background: var(--paper);
    box-shadow: 0 4px 14px rgba(0,0,0,.18);
    overflow: hidden;
  }
  .brand {
    position: absolute; left: 0; right: 0; top: 0; height: 130px;
    display: flex; align-items: center; justify-content: center;
  }
  .brand__name {
    color: var(--maroon); font-weight: 600; font-size: 30px; letter-spacing: .5px;
  }
  .photo {
    position: absolute; left: 0; top: 130px; width: 360px; height: 220px;
    background: linear-gradient(160deg, #f3ead9 0%, #f2d35a 35%, #e9c3b8 65%, #8fbf6a 100%);
  }
  .intro {
    position: absolute; left: 0; top: 345px; width: 360px; height: 110px;
    background: var(--teal); color: var(--white);
    text-align: center; padding-top: 14px;
  }
  .intro__title { font-weight: 800; font-size: 27px; letter-spacing: .5px; line-height: 1.1; }
  .intro__line { font-size: 14px; line-height: 1.3; }
  .note {
    position: absolute; left: 0; color: var(--white);
    font-size: 15px; font-weight: 600; line-height: 1.25;
    display: flex; align-items: center; justify-content: center; text-align: center;
  }
  .note--staff { top: 468px; width: 240px; height: 86px; background: var(--magenta); }
  .note--signup { top: 562px; width: 262px; height: 80px; background: var(--orange); }
  .mascot {
    position: absolute; left: 280px; top: 472px; width: 64px; height: 80px;
    background: radial-gradient(circle at 50% 40%, #8a3a24 0%, #c87a4a 55%, #f2f2f2 75%);
    border-radius: 40%;
  }
  .brand-mini {
    position: absolute; left: 270px; top: 562px; width: 86px;
    text-align: center; color: var(--maroon); font-weight: 600; font-size: 13px; line-height: 1.2;
  }
  .contact {
    position: absolute; left: 0; top: 650px; width: 360px; height: 58px;
    background: var(--blue); color: var(--white);
    display: flex; align-items: center; justify-content: center; gap: 12px;
  }
  .contact__phone { font-weight: 700; font-size: 30px; letter-spacing: .5px; }
  .web {
    position: absolute; left: 0; right: 0; top: 716px;
    text-align: center; color: var(--ink); font-weight: 700; font-size: 16px;
  }
</style>
</head>
<body>
  <main class="flyer">
    <header class="brand">
      <span class="brand__name">Felmriks Spielhafen</span>
    </header>

    <div class="photo" role="img" aria-label="Foto: zwei Kleinkinder spielen mit bunten Stapelringen und Spielzeugauto in einem Kita-Gruppenraum"></div>

    <section class="intro">
      <h1 class="intro__title">BABY-KIND-SPIELGRUPPE</h1>
      <p class="intro__line">jeden mittwoch in unserer Kita</p>
      <p class="intro__line">'Felmriks Spielhafen' von 09.00 Uhr bis 11.00 Uhr</p>
    </section>

    <p class="note note--staff">Die Spielgruppe wird durch<br>unser ausgebildetes<br>Fachpersonal begleitet</p>
    <p class="note note--signup">Voranmeldungen bitte<br>unter telefonisch und<br>website unter :</p>

    <div class="mascot" role="img" aria-label="Maskottchen der Kita"></div>
    <p class="brand-mini">Felmriks<br>Spielhafen</p>

    <div class="contact">
      <svg width="30" height="30" viewBox="0 0 24 24" aria-hidden="true">
        <path fill="#ffffff" d="M6.6 10.8a15.1 15.1 0 0 0 6.6 6.6l2.2-2.2a1 1 0 0 1 1-.25 11.4 11.4 0 0 0 3.6.57 1 1 0 0 1 1 1V20a1 1 0 0 1-1 1A17 17 0 0 1 3 4a1 1 0 0 1 1-1h3.5a1 1 0 0 1 1 1c0 1.25.2 2.45.57 3.57a1 1 0 0 1-.25 1z"/>
        <path fill="none" stroke="#ffffff" stroke-width="1.6" stroke-linecap="round" d="M14.5 3.5a6 6 0 0 1 6 6M14.5 7a2.6 2.6 0 0 1 2.5 2.5"/>
      </svg>
      <span class="contact__phone">0351-4827160</span>
    </div>
    <p class="web">www.felmriks-spielhafen.de</p>
  </main>
</body>
</html>
```